Blue Heron Journeys

We are a predominantly online travel agency with high-end (first/business class) clients. I'm looking to either have our existing logo revamped or a new logo created with business card layout. I prefer to work with existing logo if possible so it remains familiar with existing clientele. I have uploaded a yellow business card layout showing icons on one side of the card. I would like to keep my existing colours, not yellow. could the company name/tag line go over the icons?
Industry/Entity Type
Business
Contact Information for Business Card
Lucinda Fairley
Director
(I.A.T.A. 07715463)
(Corvano Pty. Ltd) ABN 61 574 203 918
512/18 Kendrick Lane
Wattle Reach | NSW 2577 | Australia
www.blueheronjourneys.com.au
m: + 61 (0) 417 588 130
t: + 61 (0) 2 9416 2058
e: lucinda@blueheronjourneys.com.au

```html
<!DOCTYPE html>
<html lang="en">
<head>
<meta charset="utf-8">
<title>Blue Heron Journeys — Business Card</title>
<link href="https://fonts.googleapis.com/css2?family=Open+Sans:wght@400;600;700&family=Didact+Gothic&display=swap" rel="stylesheet">
<style>
  :root {
    --backdrop: #3b322e;
    --card-white: #fbfbfa;
    --card-black: #141414;
    --ink: #111111;
    --ink-soft: #2a2a2a;
    --rule: #7d7d7d;
    --emboss: #3a3a3a;
    --emboss-rule: #4a4a4a;
  }
  * { margin: 0; padding: 0; box-sizing: border-box; }
  html, body {
    width: 1200px;
    height: 844px;
    overflow: hidden;
    background: var(--backdrop);
    font-family: "Open Sans", Arial, sans-serif;
  }
  .stage {
    position: relative;
    width: 1200px;
    height: 844px;
    display: flex;
    align-items: center;
    justify-content: center;
    gap: 40px;
  }
  .card {
    position: relative;
    width: 540px;
    height: 309px;
    border-radius: 2px;
  }
  .card--front { background: var(--card-white); color: var(--ink); }
  .card--back { background: var(--card-black); }

  .contact {
    position: absolute;
    left: 38px;
    top: 96px;
    font-size: 13px;
    line-height: 17px;
    color: var(--ink-soft);
  }
  .contact__name {
    font-weight: 700;
    font-size: 15px;
    letter-spacing: 0.3px;
    color: var(--ink);
  }
  .contact__title { margin-bottom: 2px; }
  .contact__row { display: flex; align-items: center; gap: 6px; }
  .contact__row svg { width: 10px; height: 10px; flex: none; }
  .contact__address { margin-top: 10px; }

  .brand {
    position: absolute;
    right: 40px;
    top: 168px;
    width: 250px;
    text-align: center;
  }
  .brand__name {
    font-family: "Open Sans", Arial, sans-serif;
    font-weight: 400;
    font-size: 25px;
    line-height: 30px;
    letter-spacing: 0.2px;
    color: var(--ink);
    white-space: nowrap;
  }
  .brand__rule {
    height: 1px;
    background: var(--rule);
    margin: 6px 0 4px;
  }
  .brand__tagline {
    font-family: "Didact Gothic", Arial, sans-serif;
    font-size: 13px;
    letter-spacing: 1.5px;
    color: var(--ink-soft);
    text-align: left;
    padding-left: 30px;
  }
  .card--back .brand { right: 70px; top: 120px; }
  .card--back .brand__name { color: var(--emboss); }
  .card--back .brand__rule { background: var(--emboss-rule); }
  .card--back .brand__tagline { color: var(--emboss); }
</style>
</head>
<body>
<main class="stage">
  <section class="card card--front" aria-label="Business card front">
    <div class="contact">
      <div class="contact__name">LORUM SMITH</div>
      <div class="contact__title">Managing Director</div>
      <div class="contact__row">
        <svg viewBox="0 0 10 10" aria-hidden="true"><path d="M2 0.5 L3.6 2.6 L2.7 3.6 C3.3 5 4.6 6.4 6.3 7.2 L7.3 6.3 L9.5 7.9 L8.3 9.5 C4.2 9.2 0.7 5.6 0.5 1.6 Z" fill="#111"/></svg>
        <span>888 444 0000</span>
      </div>
      <div class="contact__row">
        <svg viewBox="0 0 10 10" aria-hidden="true"><rect x="0.5" y="2" width="9" height="6.5" fill="#111"/><path d="M0.8 2.3 L5 5.6 L9.2 2.3" stroke="#fff" stroke-width="0.8" fill="none"/></svg>
        <span>info@webname.com</span>
      </div>
      <div class="contact__row">
        <svg viewBox="0 0 10 10" aria-hidden="true"><circle cx="5" cy="5" r="4.5" fill="#111"/><path d="M0.8 5 H9.2 M5 0.6 C3 3 3 7 5 9.4 M5 0.6 C7 3 7 7 5 9.4" stroke="#fff" stroke-width="0.6" fill="none"/></svg>
        <span>www.webaddress.com</span>
      </div>
      <div class="contact__address">
        421, Address line here,<br>
        Dummy Code,<br>
        45452 Country Name
      </div>
    </div>
    <div class="brand">
      <div class="brand__name">Blue Heron Journeys</div>
      <div class="brand__rule"></div>
      <div class="brand__tagline">go your own way</div>
    </div>
  </section>

  <section class="card card--back" aria-label="Business card back">
    <div class="brand">
      <div class="brand__name">Blue Heron Journeys</div>
      <div class="brand__rule"></div>
      <div class="brand__tagline">go your own way</div>
    </div>
  </section>
</main>
</body>
</html>
```